Small Business Consulting Firm Needs Letterhead

We need a letterhead for our company "Brightpath Plus". Our company does outbound calling and mailing to business owner's companies who have taken high interest loans. These loans tend to put these businesses in a big financial bind short term, and we help them find better financial options. We would like the design to match our colors of our logo. Headers and footers would look nice, but we are open. We would want it to include our address, website, phone, and email info. Our address - 2000 E. Lamar Blvd. Suite 600Website - www.safeguardtoday.comEmail - info@safeguardtoday.comPhone - 855-726-1938
Industry/Entity Type
Financial Planning
Look and feel
Each slider illustrates characteristics of the customer's brand and the style your logo design should communicate.

```html
<!DOCTYPE html>
<html lang="en">
<head>
<meta charset="utf-8">
<title>Brightpath Plus Letterhead</title>
<link rel="stylesheet" href="https://fonts.googleapis.com/css2?family=Arimo:wght@400;700&family=Montserrat:wght@400;500&display=swap">
<style>
  :root {
    --green: #5e9b35;
    --green-pale: #e5f0da;
    --green-faint: #dfebd3;
    --ink: #2b2b2b;
    --paper: #ffffff;
  }
  * { margin: 0; padding: 0; box-sizing: border-box; }
  html, body { width: 848px; height: 1200px; overflow: hidden; background: var(--paper); }
  .letterhead {
    position: relative; width: 848px; height: 1200px; overflow: hidden;
    font-family: "Arimo", Arial, sans-serif; color: var(--ink);
  }
  .rule { position: absolute; height: 3px; background: var(--green); }
  .rule--head-left { left: 0; top: 118px; width: 43px; }
  .rule--head-right { left: 268px; top: 118px; width: 580px; }
  .rule--foot-left { left: 0; top: 1158px; width: 510px; }
  .rule--foot-right { left: 755px; top: 1158px; width: 93px; }

  .brand { position: absolute; left: 55px; top: 50px; width: 205px; text-align: center; }
  .brand__mark { width: 50px; height: 50px; margin: 0 auto 32px; background: var(--green); }
  .brand__name {
    font-family: "Montserrat", sans-serif; font-weight: 400; font-size: 19px;
    letter-spacing: 2px; color: var(--ink); text-transform: uppercase; white-space: nowrap;
  }
  .brand__tag {
    font-family: "Montserrat", sans-serif; font-size: 9px; letter-spacing: 6px;
    color: var(--ink); margin-top: 1px;
  }

  .contact { position: absolute; top: 50px; right: 62px; display: flex; font-size: 14px; line-height: 21px; }
  .contact__address { text-align: right; padding-right: 6px; border-right: 1px solid #9a9a9a; }
  .contact__lines { padding-left: 8px; }
  .contact__line { display: flex; align-items: center; gap: 7px; }
  .contact__icon { width: 14px; height: 14px; flex: none; }

  .letter { position: absolute; left: 67px; top: 258px; width: 711px; }
  .letter__greeting { color: var(--green); font-weight: 700; font-size: 13.5px; margin-bottom: 30px; }
  .letter__para {
    font-size: 13.3px; line-height: 25.6px; text-align: justify; margin-bottom: 25.8px;
  }

  .closing-band { position: absolute; left: 0; top: 816px; width: 385px; height: 384px; background: var(--green-pale); }
  .closing-band__inner { position: absolute; left: 77px; top: 88px; width: 221px; height: 296px; background: var(--paper); }
  .closing-band__edge { position: absolute; left: 298px; top: 88px; width: 87px; height: 296px; background: var(--green-faint); }

  .sign-off { position: absolute; left: 67px; top: 824px; }
  .sign-off__label { font-weight: 700; font-size: 13.5px; }
  .sign-off__signature {
    width: 160px; height: 36px; margin-top: 14px; border-radius: 4px;
    background: linear-gradient(90deg, #cfd6cb, #e5f0da);
  }

  .website {
    position: absolute; left: 521px; top: 1149px; font-size: 15.5px; letter-spacing: 2px;
    color: var(--ink); white-space: nowrap;
  }
  .website__name { color: var(--green); font-weight: 700; }
</style>
</head>
<body>
<div class="letterhead">
  <div class="rule rule--head-left"></div>
  <div class="rule rule--head-right"></div>

  <div class="brand">
    <div class="brand__mark"></div>
    <div class="brand__name">Brightpath Plus</div>
    <div class="brand__tag">CONSULTING</div>
  </div>

  <div class="contact">
    <div class="contact__address">
      <div>Suite 310, 4170 W. Corwin Ave</div>
      <div>Fairmont, Ridgeview County 75412</div>
    </div>
    <div class="contact__lines">
      <div class="contact__line">
        <svg class="contact__icon" viewBox="0 0 14 14" aria-hidden="true">
          <circle cx="7" cy="7" r="6.2" fill="none" stroke="#5e9b35" stroke-width="1.2"/>
          <path d="M4.6 3.8c.4-.3.8-.2 1 .2l.5 1c.1.3 0 .6-.2.8l-.3.3c.4.9 1.1 1.6 2 2l.3-.3c.2-.2.5-.3.8-.2l1 .5c.4.2.5.6.2 1-.5.7-1.3.9-2.1.5-1.6-.8-2.9-2.1-3.7-3.7-.4-.8-.2-1.6.5-2.1z" fill="#5e9b35"/>
        </svg>
        <span>855-726-1938</span>
      </div>
      <div class="contact__line">
        <svg class="contact__icon" viewBox="0 0 14 14" aria-hidden="true">
          <circle cx="7" cy="7" r="6.2" fill="none" stroke="#5e9b35" stroke-width="1.2"/>
          <rect x="3.8" y="4.8" width="6.4" height="4.4" rx=".6" fill="#5e9b35"/>
          <path d="M3.9 5.1 7 7.3l3.1-2.2" fill="none" stroke="#fff" stroke-width=".7"/>
        </svg>
        <span>info@brightpathplus.com</span>
      </div>
    </div>
  </div>

  <div class="closing-band" aria-hidden="true">
    <div class="closing-band__inner"></div>
    <div class="closing-band__edge"></div>
  </div>

  <main class="letter">
    <p class="letter__greeting">Dear Mr. Lorem,</p>
    <p class="letter__para">Lorem ipsum dolor sit amet, consectetur adipiscing elit, sed do eiusmod tempor incididunt ut labore et dolore magna aliqua. Ut enim ad minim veniam, quis nostrud exercitation ullamco laboris nisi ut aliquip ex ea commodo consequat. Duis aute irure dolor in reprehenderit in voluptate velit esse cillum dolore eu fugiat nulla pariatur. Excepteur sint occaecat cupidatat non proident, sunt in culpa qui officia deserunt mollit anim id est laborum.</p>
    <p class="letter__para">Lorem ipsum dolor sit amet, consectetur adipiscing elit, sed do eiusmod tempor incididunt ut labore et dolore magna aliqua. Ut enim ad minim veniam, quis nostrud exercitation ullamco laboris nisi ut aliquip ex ea commodo consequat. Duis aute irure dolor in reprehenderit in voluptate velit esse cillum dolore eu fugiat nulla pariatur. Excepteur sint occaecat cupidatat non proident, sunt in culpa qui officia deserunt mollit anim id est laborum.</p>
    <p class="letter__para">Lorem ipsum dolor sit amet, consectetur adipiscing elit, sed do eiusmod tempor incididunt ut labore et dolore magna aliqua. Ut enim ad minim veniam, quis nostrud exercitation ullamco laboris nisi ut aliquip ex ea commodo consequat. Duis aute irure dolor in reprehenderit in voluptate velit esse cillum dolore eu fugiat nulla pariatur. Excepteur sint occaecat cupidatat non proident, sunt in culpa qui officia deserunt mollit anim id est laborum.</p>
    <p class="letter__para">Lorem ipsum dolor sit amet, consectetur adipiscing elit, sed do eiusmod tempor incididunt ut labore et dolore magna aliqua. Ut enim ad minim veniam, quis nostrud exercitation ullamco laboris nisi ut aliquip ex ea commodo consequat. Duis aute irure dolor in reprehenderit in voluptate velit esse cillum dolore eu fugiat nulla pariatur. Excepteur sint occaecat cupidatat non proident, sunt in culpa qui officia deserunt mollit anim id est laborum.</p>
  </main>

  <div class="sign-off">
    <p class="sign-off__label">Sincerely Your,</p>
    <div class="sign-off__signature" role="img" aria-label="Handwritten signature of Daniel Marsh"></div>
  </div>

  <div class="rule rule--foot-left"></div>
  <div class="website">www.<span class="website__name">brightpathplus</span>.com</div>
  <div class="rule rule--foot-right"></div>
</div>
</body>
</html>
```